Musical download and streaming website

hello designers, I want to start up a musical website where users can download and rate music of different genres such as RnB, Hip hop, rock, afro-pop. This website should be attractive and contemporary. There will be a search column for different songs. Music files will be mp3, mwa, and others. I like blue, gold, pink and indigo colors. My website should resemble http://tunovalt.com. There should be good imaginary of music stars on my website.

```html
<!DOCTYPE html>
<html lang="en">
<head>
<meta charset="utf-8">
<title>Cobalt Tunes</title>
<link rel="stylesheet" href="https://fonts.googleapis.com/css2?family=Raleway:wght@400;500&family=Open+Sans:wght@400;600&display=swap">
<style>
:root{
  --pink:#e5168a;
  --blue:#1565d0;
  --indigo:#4a3fd0;
  --gold:#f5c243;
  --gold-dark:#dcae45;
  --text:#3b3b3b;
  --muted:#555;
  --line:#cfcfcf;
  --white:#fff;
}
*{box-sizing:border-box;margin:0;padding:0}
html,body{width:930px;height:1200px;overflow:hidden;background:var(--white)}
body{position:relative;font-family:"Open Sans",sans-serif;color:var(--text)}
a{color:inherit;text-decoration:none}
ul{list-style:none}

.hero{position:absolute;left:0;top:0;width:930px;height:410px;overflow:hidden}
.hero-backdrop{position:absolute;inset:0;
  background:
    radial-gradient(ellipse 260px 300px at 760px 120px,rgba(150,170,255,.35),transparent 70%),
    radial-gradient(ellipse 300px 260px at 230px 330px,rgba(220,140,230,.4),transparent 70%),
    linear-gradient(90deg,#9a3fc6 0%,#7e47d4 30%,#4f55dd 60%,#2360e8 100%)}
.logo{position:absolute;left:68px;top:29px;font-family:"Raleway",sans-serif;font-weight:500;font-size:33px;color:var(--white);letter-spacing:.3px}
.main-nav{position:absolute;right:81px;top:43px;display:flex;gap:34px;font-family:"Raleway",sans-serif;font-size:14px;color:var(--white)}
.hero-title{position:absolute;left:0;width:930px;top:140px;text-align:center;font-family:"Raleway",sans-serif;font-weight:400;font-size:39px;color:var(--white)}
.hero-sub{position:absolute;left:0;width:930px;top:186px;text-align:center;font-family:"Raleway",sans-serif;font-size:20px;color:var(--white)}
.search{position:absolute;left:254px;top:228px;width:422px;height:34px;display:flex}
.search-field{flex:1;background:var(--white);display:flex;align-items:center;padding-left:10px;gap:8px;font-size:13px;color:#999}
.search-btn{width:94px;background:var(--gold);color:var(--white);font-family:"Raleway",sans-serif;font-size:15px;display:flex;align-items:center;justify-content:center}
.dots{position:absolute;top:377px;left:438px;display:flex;gap:3px}
.dots span{width:14px;height:14px;border-radius:50%;background:var(--white)}
.dots span.current{background:transparent;border:2px solid var(--white)}

.panel{position:absolute;top:444px;width:392px;height:255px;border:1px solid var(--line);border-top-width:3px}
.panel.songs{left:69px;border-top-color:var(--pink)}
.panel.artists{left:469px;border-top-color:var(--blue)}
.panel h2{position:absolute;left:26px;top:14px;font-family:"Raleway",sans-serif;font-weight:400;font-size:21px}
.songs h2{color:var(--pink)}.artists h2{color:var(--blue)}
.track-list{position:absolute;top:50px}
.track-list li{display:flex;align-items:center;gap:6px;height:25.3px;font-size:11px;color:var(--muted)}
.track-list svg{width:12px;height:16px}
.songs svg{fill:var(--pink)}.artists svg{fill:var(--blue)}

.listing-bar{position:absolute;left:64px;top:725px;width:796px;height:32px;background:var(--blue);color:var(--white);display:flex;align-items:center}
.listing-label{font-family:"Raleway",sans-serif;font-size:13.5px;padding-left:18px;width:130px}
.alphabet{display:flex;font-size:11px}
.alphabet span{width:19.7px;text-align:center}
.top100{position:absolute;right:0;top:0;width:130px;height:32px;background:var(--pink);font-size:11.5px;display:flex;align-items:center;justify-content:center}

.section-title{position:absolute;top:805px;font-family:"Raleway",sans-serif;font-weight:400;font-size:19.5px;color:#333}
.divider{position:absolute;left:457px;top:811px;width:1px;height:226px;background:var(--line)}
.rating{position:absolute}
.rating h3{font-weight:400;font-size:12px;color:#444}
.rating p{display:flex;align-items:center;gap:10px;margin-top:6px;font-size:10.5px;color:var(--blue)}
.stars{display:flex;gap:1px}
.stars svg{width:15px;height:15px;fill:var(--gold)}
.search-list{position:absolute;top:845px}
.search-list li{height:26px;display:flex;align-items:center;font-size:11.5px;color:var(--muted)}
.search-list li::before{content:"";width:5px;height:5px;border-top:1px solid #333;border-right:1px solid #333;transform:rotate(45deg);margin-right:12px}

.footer{position:absolute;left:0;top:1092px;width:930px;height:108px;background:linear-gradient(180deg,#e9c664,var(--gold-dark))}
.footer-nav{position:absolute;left:65px;top:25px;display:flex;gap:35px;font-family:"Raleway",sans-serif;font-size:14px;color:var(--white)}
.copyright{position:absolute;left:65px;top:51px;font-size:11px;color:var(--white)}
.social{position:absolute;left:742px;top:19px;display:flex;gap:2px}
.social span{width:27px;height:27px;border:1.5px solid var(--white);border-radius:50%}
</style>
</head>
<body>
<svg width="0" height="0" style="position:absolute">
  <symbol id="note" viewBox="0 0 12 16"><path d="M5 0h1.5c.5 2.5 4 3.5 4.5 6.5-.8-1.5-2.5-2.3-4.5-2.5V12.5A3 2.6 0 1 1 5 10.5z"/></symbol>
  <symbol id="star" viewBox="0 0 20 20"><path d="M10 1l2.8 5.9 6.2.8-4.6 4.3 1.2 6.3L10 15.2 4.4 18.3l1.2-6.3L1 7.7l6.2-.8z"/></symbol>
</svg>

<header class="hero">
  <div class="hero-backdrop" role="img" aria-label="Photo of a young woman with headphones enjoying music, tinted in purple and blue"></div>
  <div class="logo">Cobalt Tunes</div>
  <nav class="main-nav"><a>About</a><a>Download Song</a><a>Artists</a><a>Latest Songs</a><a>Resources</a></nav>
  <h1 class="hero-title">SEARCH YOUR MUSIC</h1>
  <p class="hero-sub">CUM SOCIS NATOQUE PENATIBUS DIS PARTURIENT</p>
  <div class="search">
    <div class="search-field">
      <svg width="16" height="16" viewBox="0 0 16 16" fill="none" stroke="#888" stroke-width="2"><circle cx="6.5" cy="6.5" r="5"/><path d="M10.5 10.5l4 4"/></svg>
      Type your music here
    </div>
    <div class="search-btn">Search</div>
  </div>
  <div class="dots"><span class="current"></span><span></span><span></span><span></span></div>
</header>

<section class="panel songs">
  <h2>Top Songs</h2>
  <ul class="track-list" style="left:30px">
    <li><svg><use href="#note"/></svg>Aliquam Curabitur iaculis</li>
    <li><svg><use href="#note"/></svg>Bempus eros Curabitur</li>
    <li><svg><use href="#note"/></svg>Sit amet magna</li>
    <li><svg><use href="#note"/></svg>Aalesuada ultrices</li>
    <li><svg><use href="#note"/></svg>Ut nisi erat fermentum</li>
    <li><svg><use href="#note"/></svg>Ael congue</li>
    <li><svg><use href="#note"/></svg>Euismod in elit Fusce</li>
  </ul>
  <ul class="track-list" style="left:212px">
    <li><svg><use href="#note"/></svg>Aliquam Curabitur iaculis</li>
    <li><svg><use href="#note"/></svg>Tempus eros</li>
    <li><svg><use href="#note"/></svg>Sit amet magna</li>
    <li><svg><use href="#note"/></svg>Aalesuada ultrices</li>
    <li><svg><use href="#note"/></svg>Ut nisi erat fermentum</li>
    <li><svg><use href="#note"/></svg>Ael congue</li>
    <li><svg><use href="#note"/></svg>Euismod in elit Fusce</li>
  </ul>
</section>

<section class="panel artists">
  <h2>Top Artists</h2>
  <ul class="track-list" style="left:25px">
    <li><svg><use href="#note"/></svg>Curabitur iaculis</li>
    <li><svg><use href="#note"/></svg>Eros Curabitur vel mi</li>
    <li><svg><use href="#note"/></svg>Sit amet magna</li>
    <li><svg><use href="#note"/></svg>Aalesuada ultrices</li>
    <li><svg><use href="#note"/></svg>Erat fermentum</li>
    <li><svg><use href="#note"/></svg>Ael congue</li>
    <li><svg><use href="#note"/></svg>Euismod in elit Fusce</li>
  </ul>
  <ul class="track-list" style="left:216px">
    <li><svg><use href="#note"/></svg>Aliquam Curabitur</li>
    <li><svg><use href="#note"/></svg>Curabitur vel mi</li>
    <li><svg><use href="#note"/></svg>Sit amet magna</li>
    <li><svg><use href="#note"/></svg>Aalesuada ultrices</li>
    <li><svg><use href="#note"/></svg>Ut nisi erat fermentum</li>
    <li><svg><use href="#note"/></svg>Ael congue</li>
    <li><svg><use href="#note"/></svg>Euismod in elit</li>
  </ul>
</section>

<nav class="listing-bar">
  <span class="listing-label">Artists Listings</span>
  <span class="alphabet"><span>A</span><span>B</span><span>C</span><span>D</span><span>E</span><span>F</span><span>G</span><span>H</span><span>I</span><span>J</span><span>K</span><span>L</span><span>M</span><span>N</span><span>O</span><span>P</span><span>Q</span><span>R</span><span>S</span><span>T</span><span>U</span><span>V</span><span>W</span><span>X</span><span>Y</span><span>Z</span></span>
  <a class="top100">TOP 100 SONGS</a>
</nav>

<h2 class="section-title" style="left:65px">Featured Songs Ratings</h2>
<div class="divider"></div>
<div class="rating" style="left:66px;top:852px"><h3>Song tittle here</h3><p><span class="stars"><svg><use href="#star"/></svg><svg><use href="#star"/></svg><svg><use href="#star"/></svg><svg><use href="#star"/></svg></span>By Joan Pell Marr</p></div>
<div class="rating" style="left:280px;top:852px"><h3>Song tittle here</h3><p><span class="stars"><svg><use href="#star"/></svg><svg><use href="#star"/></svg><svg><use href="#star"/></svg><svg><use href="#star"/></svg></span>By Joan Pell Marr</p></div>
<div class="rating" style="left:66px;top:915px"><h3>Song tittle here</h3><p><span class="stars"><svg><use href="#star"/></svg><svg><use href="#star"/></svg><svg><use href="#star"/></svg><svg><use href="#star"/></svg></span>By Joan Pell Marr</p></div>
<div class="rating" style="left:274px;top:915px"><h3>Song tittle here</h3><p><span class="stars"><svg><use href="#star"/></svg><svg><use href="#star"/></svg><svg><use href="#star"/></svg><svg><use href="#star"/></svg></span>By Joan Pell Marr</p></div>
<div class="rating" style="left:66px;top:977px"><h3>Song tittle here</h3><p><span class="stars"><svg><use href="#star"/></svg><svg><use href="#star"/></svg><svg><use href="#star"/></svg><svg><use href="#star"/></svg></span>By Joan Pell Marr</p></div>
<div class="rating" style="left:274px;top:977px"><h3>Song tittle here</h3><p><span class="stars"><svg><use href="#star"/></svg><svg><use href="#star"/></svg><svg><use href="#star"/></svg><svg><use href="#star"/></svg></span>By Joan Pell Marr</p></div>

<h2 class="section-title" style="left:494px">Last 20 Searches</h2>
<ul class="search-list" style="left:493px">
  <li>Mauris vel lacus vitae felis</li><li>Aestibulum volutpat</li><li>Etiam est</li><li>Nunc venenatis</li><li>Tristique eu</li><li>Imperdiet ac nisl</li><li>Cum sociis</li>
</ul>
<ul class="search-list" style="left:686px">
  <li>Ut nisi erat</li><li>Fermentum vel</li><li>Congue</li><li>Fusce ultricies orci</li><li>Suscipit leo massa sodales</li><li>Velit et scelerisque</li><li>Tortor at ipsu</li>
</ul>

<footer class="footer">
  <nav class="footer-nav"><a>About</a><a>Download Song</a><a>Artists</a><a>Latest Songs</a><a>Resources</a></nav>
  <p class="copyright">© 2016 Company Name &nbsp;All right reserved &nbsp;Term of Use</p>
  <div class="social"><span aria-label="Social link"></span><span aria-label="Social link"></span><span aria-label="Social link"></span><span aria-label="Social link"></span></div>
</footer>
</body>
</html>
```